Medical Clinic Group Looking for Website Design

We own and operate medical clinics and are looking looking to revamp our website. Our current website is www.brightpathcareclinics.ca We need our website to be more functional, user friendly, and easier to maintain.

```html
<!DOCTYPE html>
<html lang="en">
<head>
<meta charset="utf-8">
<title>Brightpath Care Clinics</title>
<link href="https://fonts.googleapis.com/css2?family=Poppins:wght@300;400;500;600&display=swap" rel="stylesheet">
<style>
:root{
  --teal:#35d3dc;
  --teal-dark:#2cc1cb;
  --ink:#1f1f1f;
  --text:#555;
  --dark:#161616;
  --soft:#f3fbfc;
  --grey:#6d6d6d;
}
*{box-sizing:border-box;margin:0;padding:0}
html,body{width:1200px;height:3482px;overflow:hidden;background:#fff}
body{position:relative;font-family:'Poppins',sans-serif;color:var(--ink)}
.abs{position:absolute}
a{color:inherit;text-decoration:none}
h2.section-title{font-weight:300;font-size:37px;color:var(--teal);letter-spacing:1px;text-align:center}
.kicker{font-size:17px;text-align:center;color:var(--ink)}

/* top bar */
.topbar{left:0;top:0;width:1200px;height:37px;background:#fff}
.topbar-fill{left:547px;top:0;width:653px;height:37px;background:var(--teal);clip-path:polygon(20px 0,100% 0,100% 100%,0 100%)}
.topbar-item{top:9px;font-size:12px;color:#fff;display:flex;align-items:center;gap:8px}
/* nav */
.brand{left:61px;top:46px;display:flex;align-items:center;gap:14px}
.brand-mark{width:54px;height:54px;border-radius:50%;border:3px solid var(--grey)}
.brand-name{font-size:30px;font-weight:300;color:var(--teal);white-space:nowrap}
.nav{left:427px;top:65px;display:flex;gap:35px;font-size:13px;color:#333}
.btn-nav{left:943px;top:55px;width:196px;height:37px;background:var(--teal);color:#fff;font-size:13px;display:flex;align-items:center;justify-content:center;border-radius:0 0 12px 0}

/* hero */
.hero{left:0;top:112px;width:1200px;height:591px;background:linear-gradient(100deg,#2f3d47 0%,#5d7384 45%,#a9bfcc 75%,#d4e1e8 100%)}
.hero-wave{left:0;top:112px}
.hero-tag{left:61px;top:182px;font-size:13px;color:var(--teal);letter-spacing:.3px}
.hero-title{left:61px;top:203px;font-size:58px;font-weight:300;line-height:63px;color:#fff;letter-spacing:1px}
.hero-text{left:61px;top:346px;width:560px;font-size:14px;line-height:22px;color:#fff;font-weight:300}
.booking{left:61px;top:439px;width:472px;height:37px;background:#fff;border-radius:8px 0 0 0;display:flex;align-items:center;justify-content:space-between;box-shadow:0 2px 8px rgba(0,0,0,.15)}
.booking span{padding-left:21px;font-size:13px;display:flex;align-items:center;gap:8px}
.booking b{height:37px;width:110px;background:var(--teal);color:#fff;font-weight:400;font-size:14px;display:flex;align-items:center;justify-content:center;border-radius:0 0 10px 0}
.down{left:575px;top:652px;width:44px;height:44px;background:#fff;border:3px solid var(--teal);border-radius:10px;transform:rotate(45deg)}
.down-arrow{left:584px;top:662px}

/* welcome */
.welcome-art{left:61px;top:770px}
.welcome-kicker{left:504px;top:784px;font-size:17px}
.welcome-title{left:504px;top:810px;font-size:37px;font-weight:300;color:var(--teal);line-height:45px;letter-spacing:1px}
.welcome-text{left:504px;top:905px;width:420px;font-size:13px;line-height:21px;color:var(--text)}
.welcome-text p+p{margin-top:9px}
.quick-tabs{left:948px;top:808px;width:252px}
.quick-tab{height:45px;margin-bottom:11px;background:var(--teal);color:#fff;border-radius:14px 0 0 0;display:flex;align-items:center;gap:12px;padding-left:14px;font-size:16px;letter-spacing:.5px}

/* services */
.services{left:0;top:1180px;width:1200px;height:482px;background:var(--soft)}
.circle-btn{width:48px;height:48px;border-radius:12px;transform:rotate(45deg);border:3px solid var(--teal);background:#fff}
.circle-btn.grey{border-color:#444}
.card{top:1331px;width:252px;height:263px;background:#fff;border-radius:6px;box-shadow:0 4px 18px rgba(0,0,0,.06);text-align:center;padding-top:30px}
.card.active{border:2px solid var(--teal)}
.card-icon{width:62px;height:62px;margin:0 auto;border-radius:50%;background:#e3f6f8;border:2px solid #222}
.card h3{margin-top:14px;font-size:17px;font-weight:400}
.card.active h3{color:var(--teal)}
.card p{margin:10px auto 0;width:215px;font-size:13px;line-height:21px;color:var(--text)}

/* testimonials */
.quote{left:308px;top:1824px;width:584px;text-align:center;font-size:13px;line-height:21px;color:#444}
.quote-name{left:0;top:2006px;width:1200px;text-align:center;font-size:17px;color:var(--teal);letter-spacing:.5px}

/* cta */
.cta{left:0;top:2109px;width:1200px;height:361px;background:var(--teal)}
.cta-kicker{left:0;top:2164px;width:1200px;text-align:center;font-size:17px}
.cta-title{left:0;top:2195px;width:1200px;text-align:center;font-size:37px;line-height:45px;font-weight:300;color:#fff;letter-spacing:1px}
.cta-text{left:320px;top:2300px;width:560px;text-align:center;font-size:13px;line-height:21px;color:#fff}
.cta-btn{left:489px;top:2368px;width:195px;height:38px;background:#fff;border-radius:8px 0 8px 0;font-size:13px;display:flex;align-items:center;justify-content:center}

/* news */
.news{top:2647px;width:340px}
.news-img{width:340px;height:224px;border-radius:6px}
.news-meta{position:absolute;left:24px;top:208px;height:33px;width:265px;background:var(--teal);color:#fff;font-size:13px;display:flex;align-items:center;justify-content:space-around;border-radius:8px 0 0 0}
.news-meta span{display:flex;align-items:center;gap:7px}
.news h3{margin-top:40px;font-size:19px;font-weight:400;line-height:30px}
.news p{margin-top:12px;font-size:12.5px;line-height:21px;color:var(--text)}
.news .more{margin-top:12px;font-size:17px;color:var(--teal);display:flex;align-items:center;gap:6px}

/* footer */
.footer{left:0;top:3121px;width:1200px;height:321px;background:var(--dark)}
.footer-brand{left:61px;top:3200px;display:flex;align-items:center;gap:12px}
.footer-brand .brand-mark{width:46px;height:46px}
.footer-brand .brand-name{font-size:23px}
.footer-about{left:61px;top:3284px;width:240px;font-size:12px;line-height:20px;color:#ddd}
.footer-col{top:3200px}
.footer-col h4{font-size:16px;font-weight:400;color:var(--teal)}
.footer-links{list-style:none;margin-top:18px}
.footer-links li{font-size:12px;color:#fff;margin-bottom:12px;display:flex;align-items:center;gap:14px}
.footer-links li::before{content:"";width:4px;height:4px;border-radius:50%;background:var(--teal)}
.footer-contact{margin-top:26px;font-size:12px;color:#fff}
.footer-contact div{display:flex;align-items:center;gap:10px;margin-bottom:20px}
.social{display:flex;gap:12px;margin-top:28px}
.social span{width:28px;height:28px;border-radius:50%;border:2px solid var(--teal)}
.social span:first-child{background:var(--teal)}
.copyright{left:0;top:3442px;width:1200px;height:40px;background:var(--teal);color:#fff;font-size:12px;display:flex;align-items:center;justify-content:center}
</style>
</head>
<body>

<!-- top bar -->
<div class="abs topbar"></div>
<div class="abs topbar-fill"></div>
<div class="abs topbar-item" style="left:570px">
  <svg width="16" height="16" viewBox="0 0 16 16"><circle cx="8" cy="8" r="7" fill="#fff"/><path d="M8 4v4l3 2" stroke="var(--teal)" stroke-width="1.6" fill="none"/></svg>
  Mon-Fri 8:30am - 4:00pm
</div>
<div class="abs topbar-item" style="left:785px">
  <svg width="16" height="12" viewBox="0 0 16 12"><rect x="1" y="1" width="14" height="10" fill="none" stroke="#fff" stroke-width="1.4"/><path d="M1 1l7 6 7-6" stroke="#fff" stroke-width="1.4" fill="none"/></svg>
  hello@brightpathcareclinics.ca
</div>
<div class="abs topbar-item" style="left:1006px">
  <svg width="16" height="16" viewBox="0 0 16 16"><path d="M3 2l3 0 1 4-2 1c1 2 2 3 4 4l1-2 4 1v3c-6 0-11-5-11-11z" fill="none" stroke="#fff" stroke-width="1.4"/></svg>
  +1 604-555-0142
</div>

<!-- nav -->
<div class="abs brand"><span class="brand-mark"></span><span class="brand-name">Brightpath Care</span></div>
<nav class="abs nav"><a>Locations</a><a>For Patients</a><a>For Providers</a><a>About Us</a><a>Book Online</a></nav>
<a class="abs btn-nav">Book An Appoinment</a>

<!-- hero -->
<div class="abs hero" role="img" aria-label="Photo of two medical students in white coats reading a blue folder in a clinic hallway"></div>
<svg class="abs hero-wave" width="1200" height="591" viewBox="0 0 1200 591"><path d="M0 465 C200 420 360 600 600 590 C850 580 1000 415 1200 398 L1200 591 L0 591Z" fill="#fff"/></svg>
<div class="abs hero-tag">WE'RE RENOVATING TO SERVE YOU BETTER</div>
<h1 class="abs hero-title">Exciting Things Are<br>Happening!</h1>
<p class="abs hero-text">Renovations have begun at our Riverside location! Over the next several months, we will be renovating the entire clinic to serve our existing patients better, as well as to create the space to accommodate several new physicians and specialists.</p>
<div class="abs booking"><span>Book at Cedar Grove Medical <svg width="10" height="7" viewBox="0 0 10 7"><path d="M1 1l4 4 4-4" stroke="#222" stroke-width="1.6" fill="none"/></svg></span><b>Book Now</b></div>
<div class="abs down"></div>
<svg class="abs down-arrow" width="26" height="26" viewBox="0 0 26 26"><path d="M6 9l7 7 7-7" stroke="#222" stroke-width="2.4" fill="none"/></svg>

<!-- welcome -->
<svg class="abs welcome-art" width="430" height="360" viewBox="0 0 430 360">
  <rect x="140" y="60" width="240" height="240" rx="40" transform="rotate(45 260 180)" fill="none" stroke="#666" stroke-width="10"/>
  <rect x="55" y="57" width="245" height="245" rx="42" transform="rotate(45 177 180)" fill="#fff" stroke="var(--teal)" stroke-width="10"/>
  <rect x="70" y="72" width="215" height="215" rx="34" transform="rotate(45 177 180)" fill="#d9c7b3" role="img" aria-label="Photo of a team of smiling doctors in white coats"/>
</svg>
<div class="abs welcome-kicker">Welcome To</div>
<h2 class="abs welcome-title">Brightpath Care<br>Clinics Services</h2>
<div class="abs welcome-text">
  <p>Lorem Ipsum is simply dummy text of the printing and typesetting industry. Lorem Ipsum has been the industry's standard dummy text ever since the 1500s, when an unknown printer took a galley of type and scrambled it to make a type specimen book. It has survived not only five centuries, but also the leap into electronic typesetting, remaining essentially unchanged.</p>
  <p>It was popularised in the 1960s with the release of Letraset sheets containing Lorem Ipsum passages,</p>
</div>
<div class="abs quick-tabs">
  <div class="quick-tab"><svg width="24" height="24" viewBox="0 0 24 24"><circle cx="10" cy="10" r="7" fill="none" stroke="#fff" stroke-width="2"/><path d="M15 15l7 7" stroke="#fff" stroke-width="2.4"/></svg>Find A Provider</div>
  <div class="quick-tab"><svg width="24" height="24" viewBox="0 0 24 24"><rect x="2" y="4" width="20" height="18" fill="none" stroke="#fff" stroke-width="2"/><path d="M2 9h20M7 2v4M17 2v4" stroke="#fff" stroke-width="2"/><path d="M6 13h2M11 13h2M16 13h2M6 17h2M11 17h2M16 17h2" stroke="#fff" stroke-width="2"/></svg>Book An Appointment</div>
  <div class="quick-tab"><svg width="24" height="24" viewBox="0 0 24 24"><path d="M12 23s-7-8-7-13a7 7 0 0114 0c0 5-7 13-7 13z" fill="none" stroke="#fff" stroke-width="2"/><circle cx="12" cy="10" r="2.5" fill="#fff"/></svg>Locations</div>
  <div class="quick-tab"><svg width="24" height="24" viewBox="0 0 24 24"><circle cx="9" cy="7" r="4" fill="#fff"/><path d="M1 21c0-5 4-8 8-8s8 3 8 8z" fill="#fff"/><path d="M19 10v8M15 14h8" stroke="#fff" stroke-width="2"/></svg>Patient Resources</div>
  <div class="quick-tab"><svg width="24" height="24" viewBox="0 0 24 24"><path d="M3 3h5l2 5-3 2c1 3 3 5 6 6l2-3 5 2v5C11 20 4 13 3 3z" fill="none" stroke="#fff" stroke-width="2"/></svg>Contact Us</div>
</div>

<!-- services -->
<div class="abs services"></div>
<div class="abs kicker" style="left:0;top:1233px;width:1200px">our Services</div>
<h2 class="abs section-title" style="left:0;top:1257px;width:1200px">What We Do</h2>
<div class="abs circle-btn" style="left:1035px;top:1236px"></div>
<svg class="abs" style="left:1044px;top:1248px" width="30" height="24" viewBox="0 0 30 24"><path d="M28 12H4M11 5l-7 7 7 7" stroke="#222" stroke-width="2.2" fill="none"/></svg>
<div class="abs circle-btn grey" style="left:1092px;top:1236px"></div>
<svg class="abs" style="left:1101px;top:1248px" width="30" height="24" viewBox="0 0 30 24"><path d="M2 12h24M19 5l7 7-7 7" stroke="#222" stroke-width="2.2" fill="none"/></svg>

<div class="abs card" style="left:59px"><div class="card-icon" role="img" aria-label="Family medicine icon"></div><h3>family Medicine</h3><p>Lorem Ipsum is simply dummy text of the printing and typesetting industry. Lorem Ipsum has been the industry's</p></div>
<div class="abs card active" style="left:338px"><div class="card-icon" role="img" aria-label="Women's health icon"></div><h3>Women's health</h3><p>Lorem Ipsum is simply dummy text of the printing and typesetting industry. Lorem Ipsum has been the industry's</p></div>
<div class="abs card" style="left:613px"><div class="card-icon" role="img" aria-label="Mental health icon"></div><h3>Mental health</h3><p>Lorem Ipsum is simply dummy text of the printing and typesetting industry. Lorem Ipsum has been the industry's</p></div>
<div class="abs card" style="left:888px"><div class="card-icon" role="img" aria-label="Sports medicine icon"></div><h3>Sports Medicine</h3><p>Lorem Ipsum is simply dummy text of the printing and typesetting industry. Lorem Ipsum has been the industry's</p></div>

<!-- testimonials -->
<div class="abs kicker" style="left:0;top:1741px;width:1200px">Testimonials</div>
<h2 class="abs section-title" style="left:0;top:1766px;width:1200px">What Our Patient Are Says...</h2>
<div class="abs circle-btn" style="left:185px;top:1858px"></div>
<svg class="abs" style="left:194px;top:1870px" width="30" height="24" viewBox="0 0 30 24"><path d="M28 12H4M11 5l-7 7 7 7" stroke="#222" stroke-width="2.2" fill="none"/></svg>
<div class="abs circle-btn grey" style="left:957px;top:1858px"></div>
<svg class="abs" style="left:966px;top:1870px" width="30" height="24" viewBox="0 0 30 24"><path d="M2 12h24M19 5l7 7-7 7" stroke="#222" stroke-width="2.2" fill="none"/></svg>
<p class="abs quote">One of the worst clinics I've ever seen in my life. You need to do something and change your staff and all the girls working in the reception without any exceptions. Either they hang up on you or transfer your call before you even finish what you're saying, or never call you back. I can't express how I feel about this right now! I've been trying to get an appointment for my baby for more than a week now and the person that is supposed to call me back never does! And when I call today for the million time, guess what? The internet and we will call you back! What is the purpose of having a family doctor if you always go to a walk-in clinic???</p>
<div class="abs quote-name">Lena Marchetti</div>

<!-- cta -->
<div class="abs cta"></div>
<div class="abs cta-kicker">Find A Doctor</div>
<h2 class="abs cta-title">Get Free In Schedule in An<br>Appointment Today</h2>
<p class="abs cta-text">Lorem Ipsum is simply dummy text of the printing and typesetting industry. Lorem Ipsum has been the industry's standard dummy text.</p>
<a class="abs cta-btn">Book An Appoinment</a>

<!-- news -->
<div class="abs kicker" style="left:0;top:2549px;width:1200px">Keep Updated</div>
<h2 class="abs section-title" style="left:0;top:2573px;width:1200px">news and upcoming events</h2>

<div class="abs news" style="left:59px">
  <div class="news-img" style="background:linear-gradient(135deg,#cfd3cf,#a7a59b)" role="img" aria-label="Photo of a doctor consulting a patient at a desk"></div>
  <div class="news-meta"><span><svg width="16" height="16" viewBox="0 0 16 16"><rect x="1" y="2" width="14" height="13" fill="none" stroke="#fff" stroke-width="1.5"/><path d="M1 6h14" stroke="#fff" stroke-width="1.5"/></svg>5 Oct 2022</span><span><svg width="14" height="16" viewBox="0 0 14 16"><circle cx="7" cy="4" r="3.5" fill="#fff"/><path d="M0 16c0-5 3-7 7-7s7 2 7 7z" fill="#fff"/></svg>Admin</span></div>
  <h3>Lorem Ipsum is simply dummy text of the printing</h3>
  <p>Lorem Ipsum is simply dummy text of the printing and typesetting industry.</p>
  <a class="more">Learn More <svg width="24" height="10" viewBox="0 0 24 10"><path d="M0 5h22M17 1l5 4-5 4" stroke="var(--teal)" stroke-width="1.6" fill="none"/></svg></a>
</div>
<div class="abs news" style="left:430px">
  <div class="news-img" style="background:linear-gradient(135deg,#bfe0e4,#4fa6bd)" role="img" aria-label="Photo of two medical workers looking at a tablet"></div>
  <div class="news-meta"><span><svg width="16" height="16" viewBox="0 0 16 16"><rect x="1" y="2" width="14" height="13" fill="none" stroke="#fff" stroke-width="1.5"/><path d="M1 6h14" stroke="#fff" stroke-width="1.5"/></svg>5 Oct 2022</span><span><svg width="14" height="16" viewBox="0 0 14 16"><circle cx="7" cy="4" r="3.5" fill="#fff"/><path d="M0 16c0-5 3-7 7-7s7 2 7 7z" fill="#fff"/></svg>Admin</span></div>
  <h3>Lorem Ipsum is simply dummy text of the printing</h3>
  <p>Lorem Ipsum is simply dummy text of the printing and typesetting industry.</p>
  <a class="more">Learn More <svg width="24" height="10" viewBox="0 0 24 10"><path d="M0 5h22M17 1l5 4-5 4" stroke="var(--teal)" stroke-width="1.6" fill="none"/></svg></a>
</div>
<div class="abs news" style="left:800px">
  <div class="news-img" style="background:linear-gradient(135deg,#c8dbe6,#e8c7a6)" role="img" aria-label="Photo of a doctor greeting a child patient"></div>
  <div class="news-meta"><span><svg width="16" height="16" viewBox="0 0 16 16"><rect x="1" y="2" width="14" height="13" fill="none" stroke="#fff" stroke-width="1.5"/><path d="M1 6h14" stroke="#fff" stroke-width="1.5"/></svg>5 Oct 2022</span><span><svg width="14" height="16" viewBox="0 0 14 16"><circle cx="7" cy="4" r="3.5" fill="#fff"/><path d="M0 16c0-5 3-7 7-7s7 2 7 7z" fill="#fff"/></svg>Admin</span></div>
  <h3>Lorem Ipsum is simply dummy text of the printing</h3>
  <p>Lorem Ipsum is simply dummy text of the printing and typesetting industry.</p>
  <a class="more">Learn More <svg width="24" height="10" viewBox="0 0 24 10"><path d="M0 5h22M17 1l5 4-5 4" stroke="var(--teal)" stroke-width="1.6" fill="none"/></svg></a>
</div>

<!-- footer -->
<footer class="abs footer"></footer>
<div class="abs footer-brand"><span class="brand-mark"></span><span class="brand-name">Brightpath Care</span></div>
<p class="abs footer-about">Renovations have begun at our Riverside location! Over the next several months, we will be renovating the entire clinic.</p>
<div class="abs footer-col" style="left:339px;width:200px">
  <h4>Quick Links</h4>
  <ul class="footer-links"><li>Locations</li><li>For Patients</li><li>For Providers</li><li>About Us</li><li>Book Online</li><li>Contact Us</li></ul>
</div>
<div class="abs footer-col" style="left:615px;width:240px">
  <h4>Contact Us</h4>
  <div class="footer-contact">
    <div><svg width="18" height="18" viewBox="0 0 18 18"><path d="M3 2h4l1 4-2 1c1 2 3 4 5 5l1-2 4 1v4C9 15 3 9 3 2z" fill="none" stroke="var(--teal)" stroke-width="1.5"/></svg>+1 604-555-0142</div>
    <div><svg width="18" height="14" viewBox="0 0 18 14"><rect x="1" y="1" width="16" height="12" fill="none" stroke="var(--teal)" stroke-width="1.5"/><path d="M1 1l8 7 8-7" stroke="var(--teal)" stroke-width="1.5" fill="none"/></svg>hello@brightpathcareclinics.ca</div>
  </div>
</div>
<div class="abs footer-col" style="left:890px;width:220px">
  <h4>Connect With Us</h4>
  <div class="social"><span></span><span></span><span></span></div>
</div>
<div class="abs copyright">©2022 by Brightpath Care Clinics. All Right Reserved.</div>

</body>
</html>
```